Health and Wellness company needs flyer to promote free seminar

Corvella Motion studio is a health and wellness company that offers an exercise program designed by physical therapists to help relieve pain and improve mobility. Our business is a new concept that is not well understood by the public. In order to promote our business we offer a free seminar where we present information regarding the underlying cause of pain and tightness. During the seminar we also perform a posture screen and movement testing for all participants.

Target Market(s)

Mostly healthy and active women ages 25-65

Industry/Entity Type

Health And Wellness

Font styles to use
Sans Serif

Colors

Designer to choose colors to be used in the design.

Requirements
Must have
• Title: Eliminate Pain and Tightness For Good
• Paragraph: Corvella Motion Studio offers a free 60 minute seminar: "The Busy Walker's Manual for Stretching and Living Lighter."
• What to Expect:
• • Identify the underlying cause of your pain and mobility issues
• • Expose what gets in the way of you moving and feeling better
• • Learn why traditional exercises don’t help and can actually make the problem worse
• • Reveal what your posture is saying and how that impacts you
• • Experience your muscle imbalances through movement tests
• • Discover the training method that realigns your posture, increases your mobility and reduces your pain
• Call to action: RSVP online at corvellamotionstudio.com
Nice to have
• Use a relevant image showing a female dealing with tightness in the low back, legs, etc.
• Emphasize that the seminar is FREE.
• Make the call to action prominent.

```html
<!DOCTYPE html>
<html lang="en">
<head>
<meta charset="utf-8">
<title>Corvella Motion Studio – Free 60 Minute Seminar</title>
<link rel="stylesheet" href="https://fonts.googleapis.com/css2?family=Open+Sans:wght@300;400;600;700;800&display=swap">
<style>
  :root{
    --purple:#5a5ea9;
    --orange:#f7941d;
    --orange-deep:#ee8512;
    --white:#ffffff;
    --paper:#f1f1f1;
    --footer:#8a8a8a;
    --photo-a:#d9d4d2;
    --photo-b:#a9a6ab;
  }
  *{margin:0;padding:0;box-sizing:border-box}
  html,body{width:845px;height:1200px;overflow:hidden;background:var(--white)}
  body{font-family:"Open Sans",Arial,sans-serif;color:var(--white)}
  .flyer{position:relative;width:845px;height:1200px;overflow:hidden;background:var(--paper)}
  .backdrop{position:absolute;inset:0}
  .brand{position:absolute;left:24px;top:26px;display:flex;align-items:center;gap:14px}
  .brand-mark{width:52px;height:52px;background:var(--orange)}
  .brand-name{font-weight:600;font-size:30px;color:var(--purple);letter-spacing:-0.3px}
  .headline-band{position:absolute;left:-42px;top:273px;width:760px;height:54px;background:var(--orange);
    transform:rotate(30.6deg);display:flex;align-items:center;justify-content:center;
    box-shadow:0 2px 6px rgba(0,0,0,.18)}
  .headline-band h1{font-weight:700;font-size:33px;color:var(--white);white-space:nowrap;padding-left:70px}
  .offer{position:absolute;left:28px;top:318px;line-height:1}
  .offer .free{font-weight:800;font-size:66px;display:block}
  .offer .length{font-weight:300;font-size:64px;display:block;margin-top:10px}
  .offer .kind{font-weight:700;font-size:50px;display:block;margin-top:6px}
  .expect{position:absolute;left:30px;top:553px;width:500px}
  .expect h2{font-weight:300;font-size:32px;margin-bottom:22px}
  .expect ul{list-style:none}
  .expect li{position:relative;padding-left:24px;font-size:14.3px;line-height:19px;margin-bottom:18px}
  .expect li svg{position:absolute;left:0;top:3px}
  .expect li strong{font-weight:700;text-decoration:underline}
  .photo-circle{position:absolute;border-radius:50%;border:6px solid var(--white);box-shadow:0 2px 8px rgba(0,0,0,.15)}
  .circle-session{left:612px;top:488px;width:200px;height:200px;background:linear-gradient(135deg,#e8dccf,#b9a79a)}
  .circle-shoulder{left:530px;top:710px;width:200px;height:200px;background:linear-gradient(135deg,#f2e6dc,#c7b8ae)}
  .circle-runners{left:425px;top:925px;width:200px;height:200px;background:linear-gradient(180deg,#d9c7a8,#8e7c6a)}
  .quote-mark{position:absolute;left:22px;top:985px;font-weight:800;font-size:110px;color:#fbb464;line-height:1}
  .seminar-title{position:absolute;left:44px;top:1050px;width:380px;font-weight:700;font-size:22px;line-height:31px}
  .rsvp{position:absolute;left:0;bottom:0;width:845px;height:40px;background:var(--footer);
    display:flex;align-items:center;justify-content:center;gap:12px;font-size:16px;font-weight:400;letter-spacing:.3px}
</style>
</head>
<body>
<main class="flyer">
  <svg class="backdrop" width="845" height="1200" viewBox="0 0 845 1200">
    <defs>
      <linearGradient id="treatment-tone" x1="0" y1="0" x2="1" y2="1">
        <stop offset="0" stop-color="var(--photo-a)"/>
        <stop offset="1" stop-color="var(--photo-b)"/>
      </linearGradient>
    </defs>
    <rect width="845" height="1200" fill="var(--paper)"/>
    <polygon points="0,0 845,0 845,300 0,140" fill="var(--white)"/>
    <polygon role="img" aria-label="Therapist gently stretching a woman's neck and shoulder" points="240,0 845,0 845,500 720,540 300,300" fill="url(#treatment-tone)"/>
    <polygon points="0,165 735,545 500,965 0,880" fill="var(--purple)"/>
    <polygon points="0,880 500,965 440,1160 0,1160" fill="var(--orange)"/>
  </svg>

  <header class="brand">
    <span class="brand-mark"></span>
    <span class="brand-name">Corvella Motion Studio</span>
  </header>

  <div class="headline-band"><h1>Eliminate Pain &amp; Tightness For Good</h1></div>

  <section class="offer">
    <span class="free">FREE</span>
    <span class="length">60 minute</span>
    <span class="kind">seminar</span>
  </section>

  <section class="expect">
    <h2>What To Expect</h2>
    <ul>
      <li><svg width="14" height="12" viewBox="0 0 14 12"><path d="M1 6.5 5 10 13 1.5" fill="none" stroke="var(--orange)" stroke-width="2"/></svg><strong>Identify</strong> the underlying cause of your pain and mobility issues</li>
      <li><svg width="14" height="12" viewBox="0 0 14 12"><path d="M1 6.5 5 10 13 1.5" fill="none" stroke="var(--orange)" stroke-width="2"/></svg><strong>Expose</strong> what gets in the way of you moving and feeling better</li>
      <li><svg width="14" height="12" viewBox="0 0 14 12"><path d="M1 6.5 5 10 13 1.5" fill="none" stroke="var(--orange)" stroke-width="2"/></svg><strong>Learn</strong> why traditional exercises don’t help and can actually make the problem worse</li>
      <li><svg width="14" height="12" viewBox="0 0 14 12"><path d="M1 6.5 5 10 13 1.5" fill="none" stroke="var(--orange)" stroke-width="2"/></svg><strong>Reveal</strong> what your posture is saying and how that impacts you</li>
      <li><svg width="14" height="12" viewBox="0 0 14 12"><path d="M1 6.5 5 10 13 1.5" fill="none" stroke="var(--orange)" stroke-width="2"/></svg><strong>Experience</strong> your muscle imbalances through movement tests</li>
      <li><svg width="14" height="12" viewBox="0 0 14 12"><path d="M1 6.5 5 10 13 1.5" fill="none" stroke="var(--orange)" stroke-width="2"/></svg><strong>Discover</strong> the training method that realigns your posture, increases your mobility and reduces your pain</li>
    </ul>
  </section>

  <div class="photo-circle circle-session" role="img" aria-label="Trainer assisting a woman with a leg stretch in the studio"></div>
  <div class="photo-circle circle-shoulder" role="img" aria-label="Woman holding a tight shoulder"></div>
  <div class="photo-circle circle-runners" role="img" aria-label="Two people jogging outdoors at sunrise"></div>

  <span class="quote-mark" aria-hidden="true">“</span>
  <p class="seminar-title">The Busy Walker's Manual for Stretching and Living Lighter</p>

  <footer class="rsvp">
    <svg width="20" height="20" viewBox="0 0 20 20" aria-hidden="true">
      <circle cx="10" cy="10" r="9" fill="var(--white)"/>
      <path d="M6 5c2 1 1 3 3 3s1 3 0 4-1 3-2 3M13 4c-1 2 1 3 3 3M12 13c1-1 3-1 4 0" fill="none" stroke="var(--footer)" stroke-width="1.6"/>
    </svg>
    <span>RSVP ONLINE at corvellamotionstudio.com</span>
  </footer>
</main>
</body>
</html>
```